VENTURE CAPITAL GROUP BUSINESS CARD DESIGN

Venture Capital Group based in SF looking for a bold business card design. No trendy colour explosion, 3D effects etc. Just "simple" optical effects. Works on your brain, keeps your eye focused and sticks to your mind.
Target Market(s)
Technology startups
Industry/Entity Type
Venture Capital
Contact Information for Business Card
DESMOND WHITLAKE
MANAGING PARTNER
187 FENWORTH ST SAN FRANCISCO, CA 94187
415.555.0142 O
415.555.0147 F
415.555.0193 C
desmond@veldtmoorcapital.ventures

```html
<!DOCTYPE html>
<html lang="en">
<head>
<meta charset="utf-8">
<title>Veldtmoor Capital Group – Business Card</title>
<link rel="stylesheet" href="https://fonts.googleapis.com/css2?family=Open+Sans:wght@400;600;700&display=swap">
<style>
  :root {
    --bg: #2b2b2d;
    --card: #ffffff;
    --green-dark: #0f4d24;
    --green-bright: #39b54a;
    --brand-green: #1f7a34;
    --disc: #e4e4e4;
    --white: #ffffff;
  }
  * { box-sizing: border-box; margin: 0; padding: 0; }
  html, body { width: 1200px; height: 900px; overflow: hidden; }
  body {
    background: var(--bg);
    font-family: "Open Sans", sans-serif;
    position: relative;
  }
  .card {
    position: absolute;
    left: 250px;
    width: 700px;
    height: 400px;
    background: var(--card);
    border-radius: 26px;
    overflow: hidden;
  }
  .card--front { top: 40px; }
  .card--back { top: 460px; }

  .brand {
    position: absolute;
    display: flex;
    flex-direction: column;
    align-items: center;
    text-align: center;
  }
  .brand__disc {
    border-radius: 50%;
    background: var(--disc);
  }
  .brand__name {
    color: var(--brand-green);
    font-weight: 600;
    letter-spacing: 0.06em;
    text-transform: uppercase;
    line-height: 1.25;
  }
  .card--front .brand { left: 0; right: 0; top: 90px; }
  .card--front .brand__disc { width: 130px; height: 130px; margin-bottom: 22px; }
  .card--front .brand__name { font-size: 34px; }

  .card--back .brand { left: 505px; width: 180px; top: 110px; }
  .card--back .brand__disc { width: 84px; height: 84px; margin-bottom: 14px; }
  .card--back .brand__name { font-size: 20px; }

  .back__panel { position: absolute; inset: 0; }

  .contact {
    position: absolute;
    left: 48px;
    top: 118px;
    color: var(--white);
  }
  .contact__name {
    font-size: 29px;
    font-weight: 700;
    letter-spacing: 0.02em;
    line-height: 1.1;
  }
  .contact__title {
    font-size: 16px;
    font-weight: 600;
    color: var(--green-bright);
    letter-spacing: 0.04em;
    margin-bottom: 10px;
  }
  .contact__address {
    font-size: 16px;
    line-height: 1.3;
    margin-bottom: 8px;
  }
  .contact__list { list-style: none; }
  .contact__item {
    display: flex;
    align-items: center;
    gap: 12px;
    font-size: 16px;
    line-height: 1.4;
  }
  .contact__icon { width: 14px; height: 14px; flex: none; }
</style>
</head>
<body>

<section class="card card--front" aria-label="Card front">
  <div class="brand">
    <div class="brand__disc"></div>
    <p class="brand__name">Veldtmoor<br>Capital Group</p>
  </div>
</section>

<section class="card card--back" aria-label="Card back">
  <svg class="back__panel" width="700" height="400" viewBox="0 0 700 400" aria-hidden="true">
    <path d="M0 0 H340 C470 70 520 290 420 400 H0 Z" fill="var(--green-bright)"/>
    <path d="M0 0 H326 C454 70 504 290 406 400 H0 Z" fill="var(--green-dark)"/>
  </svg>

  <div class="contact">
    <h1 class="contact__name">DESMOND WHITLAKE</h1>
    <p class="contact__title">MANAGING PARTNER</p>
    <p class="contact__address">187 FENWORTH ST SAN<br>FRANCISCO, CA 94187</p>
    <ul class="contact__list">
      <li class="contact__item">
        <svg class="contact__icon" viewBox="0 0 16 16" aria-label="Office"><path d="M3 1h3l1.5 4-2 1.2a9 9 0 0 0 4.3 4.3L11 8.5l4 1.5v3a2 2 0 0 1-2 2A12 12 0 0 1 1 3a2 2 0 0 1 2-2z" fill="var(--green-bright)"/></svg>
        415.555.0142
      </li>
      <li class="contact__item">
        <svg class="contact__icon" viewBox="0 0 16 16" aria-label="Fax"><rect x="4" y="1" width="8" height="5" fill="var(--green-bright)"/><rect x="1" y="6" width="14" height="7" rx="1.5" fill="var(--green-bright)"/><rect x="4" y="11" width="8" height="4" fill="var(--green-bright)"/></svg>
        415.555.0147
      </li>
      <li class="contact__item">
        <svg class="contact__icon" viewBox="0 0 16 16" aria-label="Cell"><rect x="4" y="1" width="8" height="14" rx="1.5" fill="none" stroke="var(--green-bright)" stroke-width="1.6"/><circle cx="8" cy="12.3" r="0.9" fill="var(--green-bright)"/></svg>
        415.555.0193
      </li>
      <li class="contact__item">
        <svg class="contact__icon" viewBox="0 0 16 16" aria-label="Email"><rect x="1" y="3" width="14" height="10" rx="1" fill="none" stroke="var(--green-bright)" stroke-width="1.6"/><path d="M1.5 3.8 8 9l6.5-5.2" fill="none" stroke="var(--green-bright)" stroke-width="1.6"/></svg>
        desmond@veldtmoorcapital.ventures
      </li>
    </ul>
  </div>

  <div class="brand">
    <div class="brand__disc"></div>
    <p class="brand__name">Veldtmoor<br>Capital Group</p>
  </div>
</section>

</body>
</html>
```